Business Card Design Project : Ridgeline Press

In preparation for market launch, Tamarind's Ridgeline Press require the development of a business card. Ridgeline Press is a Community online publishing web portal. We provide the the city of Whistler located in B.C. (Canada) business directories, News, Classified ads, News, Events and blogs etc.

The main focus of the brand is to help local businesses to corporate with their online advertisement and marketing. Meeting our clients face to face is a must (B2B).

Target Market(s)

The target market is B2B customers. Business Owners to Marketing, advertising Managers

Industry/Entity Type

Business

Requirements
Must have
• - The business card will be two sided.
the BACK side will have our logo which consist of (icon, url,slogan) submited. The logo will be middle and centred.

The FRONT side should have company details:

Company Legal Name: TAMARIND RIDGELINE MEDIA

Owen Farsk
Director of Sales & Marketing

www.tamarindridgeline.biz
owen@tamarindridgeline.biz

Phone: 604 317 8842
#2714 - 582 E. Halvern St.
Vancouver, B.C. V7K2R4 Canada
Nice to have
• - For the "FRONT" side of our business card. You can separate or re-arrange with our logo components (icon, logo,slogan). It does not have to be together.

Also our company legal name is rather long so arrange or organize the name in a way to make it shorter. Your experience and creativity will have to come in play.
Should not have
• should not have other colors beside logo color and black text (2 colors). Also nothing Three dimensional

```html
<!DOCTYPE html>
<html lang="en">
<head>
<meta charset="utf-8">
<title>Ridgeline Press — Business Card</title>
<link rel="stylesheet" href="https://fonts.googleapis.com/css2?family=Open+Sans:ital,wght@0,400;0,600;0,700;1,400&display=swap">
<style>
  :root {
    --brand-blue: #1f72b8;
    --brand-blue-light: #3d8fd0;
    --ink: #1a1a1a;
    --ink-soft: #333333;
    --paper: #ffffff;
    --paper-shade: #ececec;
    --backdrop: #e4e6e9;
  }
  * { margin: 0; padding: 0; box-sizing: border-box; }
  html, body {
    width: 1200px;
    height: 944px;
    overflow: hidden;
  }
  body {
    background: var(--backdrop);
    font-family: "Open Sans", Arial, sans-serif;
    position: relative;
  }
  .card {
    position: absolute;
    width: 640px;
    height: 366px;
    border-radius: 18px;
    overflow: hidden;
    box-shadow: 0 6px 18px rgba(0,0,0,0.18);
  }

  /* Back side */
  .card-back {
    left: 70px;
    top: 70px;
    background: radial-gradient(ellipse at 45% 40%, var(--brand-blue-light) 0%, var(--brand-blue) 70%);
    color: var(--paper);
  }
  .card-back .brand-name {
    position: absolute;
    left: 0; right: 0;
    top: 70px;
    text-align: center;
    font-size: 52px;
    font-weight: 700;
    color: var(--paper);
    letter-spacing: 0.5px;
  }
  .card-back .brand-url {
    position: absolute;
    left: 0; right: 0;
    top: 172px;
    text-align: center;
    font-size: 37px;
    font-weight: 700;
    color: var(--ink);
    letter-spacing: -0.3px;
  }
  .card-back .brand-slogan {
    position: absolute;
    left: 0; right: 0;
    top: 222px;
    text-align: center;
    font-size: 30px;
    font-weight: 400;
    color: var(--paper);
  }

  /* Front side */
  .card-front {
    left: 490px;
    top: 508px;
    background: linear-gradient(160deg, var(--paper) 0%, var(--paper) 55%, var(--paper-shade) 100%);
    color: var(--ink);
  }
  .card-front .edge-stripe {
    position: absolute;
    top: 0; bottom: 0; right: 0;
    width: 14px;
    background: var(--brand-blue);
  }
  .card-front .brand-name {
    position: absolute;
    left: 0; right: 0;
    top: 36px;
    text-align: center;
    font-size: 40px;
    font-weight: 700;
    color: var(--brand-blue);
  }
  .card-front .brand-slogan {
    position: absolute;
    left: 0; right: 0;
    top: 100px;
    text-align: center;
    font-size: 19px;
    color: var(--ink);
  }
  .card-front .person {
    position: absolute;
    left: 34px;
    top: 162px;
  }
  .card-front .person-name {
    font-size: 24px;
    font-weight: 600;
    color: var(--brand-blue);
    line-height: 1.2;
  }
  .card-front .person-title {
    font-size: 15px;
    font-style: italic;
    color: var(--ink-soft);
  }
  .card-front .url-band {
    position: absolute;
    right: 0;
    top: 196px;
    width: 292px;
    height: 40px;
    background: var(--brand-blue);
    color: var(--paper);
    font-size: 17px;
    font-weight: 700;
    line-height: 40px;
    padding-left: 16px;
  }
  .card-front .address {
    position: absolute;
    left: 34px;
    top: 262px;
    font-size: 16px;
    line-height: 1.45;
    color: var(--ink);
    display: flex;
    gap: 8px;
  }
  .card-front .contact {
    position: absolute;
    left: 362px;
    top: 262px;
    font-size: 16px;
    line-height: 1.45;
    color: var(--ink);
  }
  .contact-line {
    display: flex;
    align-items: center;
    gap: 10px;
  }
  .icon {
    width: 16px;
    height: 16px;
    flex: none;
    fill: var(--brand-blue);
  }
</style>
</head>
<body>

  <section class="card card-back" aria-label="Business card, back side">
    <div class="brand-name">Ridgeline Press</div>
    <div class="brand-url">www.tamarindridgeline.biz</div>
    <div class="brand-slogan">Your information gateway</div>
  </section>

  <section class="card card-front" aria-label="Business card, front side">
    <div class="edge-stripe"></div>
    <div class="brand-name">Ridgeline Press</div>
    <div class="brand-slogan">Your information gateway</div>

    <div class="person">
      <div class="person-name">Owen Farsk</div>
      <div class="person-title">Director of Sales &amp; Marketing</div>
    </div>

    <div class="url-band">www.tamarindridgeline.biz</div>

    <div class="address">
      <svg class="icon" viewBox="0 0 16 16" aria-hidden="true" style="margin-top:3px">
        <path d="M8 1 L15 8 H13 V15 H10 V10 H6 V15 H3 V8 H1 Z"/>
      </svg>
      <div>#2714 - 582 E. Halvern St.<br>Vancouver, B.C. V7K2R4 Canada</div>
    </div>

    <div class="contact">
      <div class="contact-line">
        <svg class="icon" viewBox="0 0 16 16" aria-hidden="true">
          <path d="M3.5 1 L6 1 L7 4.5 L5.3 5.8 C6 7.6 8.4 10 10.2 10.7 L11.5 9 L15 10 L15 12.5 C15 13.9 13.9 15 12.5 15 C6.7 15 1 9.3 1 3.5 C1 2.1 2.1 1 3.5 1 Z"/>
        </svg>
        <span>604 317 8842</span>
      </div>
      <div class="contact-line">
        <svg class="icon" viewBox="0 0 16 16" aria-hidden="true">
          <path d="M1 4 H15 V13 H1 Z M1.5 4.5 L8 9.5 L14.5 4.5" fill="none" stroke="#1f72b8" stroke-width="1.6" stroke-linejoin="round"/>
        </svg>
        <span>owen@tamarindridgeline.biz</span>
      </div>
    </div>
  </section>

</body>
</html>
```